VIRTUAL KIDS PARTIES for ages 3-10 years

I need a very urgent leaflet, that looks fun and eye catching aimed at ages 3-10 years.

Award winning, accredited, performing arts provider KPM are excited to bring you LIVE interactive drama, singing and dance parties taught by industry qualified performers that can be accessed from home.

* A chance for your child to hook up with their classmates and friends.

* An interactive hour of games, dancing and singing amongst friends as you talk, laugh and play together on screen.

* Tailor made themes, music choices and routines.

* A chance to socialise in a safe environment and celebrate that special day.

* All staff are qualified, DBS checked industry professionals and teachers.

* Flexible times to suit.

Packages start from £65 plus vat

Visit www.brightstagehub.co.uk to book
Check out our online performing arts classes and interactive sessions.

Target Market(s)

Parents and children ages 3-10 years

Colors
ef3f46
ffc214
faa54b
33a6d7
87d0c7
abd037

Requirements
Must have
• Clear text that this is a service for ONLINE VIRTUAL parties

Should be upbeat, happy, bright & vibrant

Logo ( attached)

MUST LOOK PROFESSIONAL

Photo or clever art designs if designer can do this

See attached photos and leaflets for inspiration
Nice to have
• Emphasis on Dance, drama, musical theatre, singing

```html
<!DOCTYPE html>
<html lang="en">
<head>
<meta charset="utf-8">
<title>Bright Stage – Virtual Kids Parties</title>
<link rel="stylesheet" href="https://fonts.googleapis.com/css2?family=Amatic+SC:wght@700&family=Baloo+2:wght@600;700;800&family=Nunito:wght@400;600&display=swap">
<style>
:root{
  --red:#ef3f46;
  --yellow:#ffc214;
  --orange:#faa54b;
  --blue:#33a6d7;
  --teal:#87d0c7;
  --green:#abd037;
  --ink:#0d0b0c;
  --white:#ffffff;
  --page:#ffffff;
}
*{box-sizing:border-box;margin:0;padding:0}
html,body{width:1200px;height:2949px;overflow:hidden;background:var(--page)}
.leaflet{
  position:absolute;left:105px;top:1342px;width:990px;height:1403px;
  background:var(--ink);overflow:hidden;
  box-shadow:0 6px 18px rgba(0,0,0,.25);
  font-family:"Nunito",sans-serif;color:var(--white);
}
.stage-photo{
  position:absolute;left:0;top:300px;width:990px;height:700px;
  background:
    radial-gradient(ellipse at 30% 30%,rgba(120,40,90,.35),transparent 60%),
    radial-gradient(ellipse at 75% 40%,rgba(60,70,140,.3),transparent 60%),
    radial-gradient(ellipse at 50% 20%,rgba(150,90,40,.25),transparent 55%);
}
.headline{
  position:absolute;left:55px;top:40px;
  font-family:"Amatic SC",cursive;font-weight:700;
  font-size:92px;line-height:88px;letter-spacing:1px;text-transform:uppercase;
}
.headline .red{color:var(--red)}
.headline .green{color:var(--green)}
.brand{
  position:absolute;left:640px;top:120px;display:flex;align-items:center;gap:16px;
}
.brand-dot{width:70px;height:70px;border-radius:50%;background:var(--yellow)}
.brand-name{font-family:"Baloo 2",sans-serif;font-weight:800;font-size:56px;color:var(--red);line-height:1}
.tags{position:absolute;left:55px;top:338px}
.tag{
  display:block;width:max-content;margin-bottom:6px;padding:0 20px 0 8px;
  height:46px;line-height:50px;border-radius:0 24px 24px 0;
  font-family:"Baloo 2",sans-serif;font-weight:700;font-size:38px;color:var(--white);
}
.tag.blue{background:var(--blue)}
.tag.yellow{background:var(--yellow)}
.tag.red{background:var(--red)}
.intro{
  position:absolute;left:55px;top:500px;width:470px;
  font-size:23px;line-height:28px;
}
.features{position:absolute;left:50px;top:668px;list-style:none}
.feature{display:flex;align-items:center;gap:30px;position:absolute;left:0;width:max-content}
.feature svg{flex:0 0 62px}
.feature p{font-size:21px;line-height:25px;white-space:nowrap}
.swoosh{position:absolute;left:0;top:0}
.party-art{
  position:absolute;left:560px;top:650px;width:400px;height:540px;border-radius:24px;
  background:linear-gradient(160deg,#f3f3f3,#dfe3e8 60%,#cfd8ea);
}
.screen-art{
  position:absolute;left:425px;top:960px;width:230px;height:200px;border-radius:10px;
  background:linear-gradient(160deg,#5a4a48,#2b2d33 60%,#bfc3c8);
}
.balloons{
  position:absolute;left:535px;top:370px;width:450px;height:270px;border-radius:140px;
  background:radial-gradient(circle at 20% 40%,rgba(51,166,215,.7),transparent 40%),
             radial-gradient(circle at 82% 30%,rgba(120,110,230,.7),transparent 40%),
             radial-gradient(circle at 18% 80%,rgba(250,165,75,.6),transparent 35%);
}
.price{
  position:absolute;left:640px;top:358px;width:260px;height:260px;border-radius:50%;
  background:var(--white);border:5px solid var(--orange);
  text-align:center;font-family:"Baloo 2",sans-serif;
}
.price .lead{color:var(--blue);font-weight:700;font-size:32px;line-height:34px;margin-top:32px}
.price .amount{color:var(--red);font-weight:800;font-size:86px;line-height:74px}
.price .vat{color:var(--red);font-weight:700;font-size:30px;line-height:32px}
.book-pill{
  position:absolute;left:805px;top:1158px;padding:0 18px;height:40px;line-height:44px;
  background:var(--teal);border-radius:20px;
  font-family:"Baloo 2",sans-serif;font-weight:700;font-size:28px;color:var(--white);
}
.visit-bar{
  position:absolute;left:340px;top:1196px;width:625px;height:76px;border-radius:38px;
  background:var(--red);display:flex;align-items:center;gap:12px;padding-left:24px;
  font-family:"Baloo 2",sans-serif;font-weight:700;font-size:35px;color:var(--white);white-space:nowrap;
}
.sessions{
  position:absolute;left:345px;top:1290px;width:620px;text-align:center;
  font-family:"Baloo 2",sans-serif;font-weight:600;font-size:31px;line-height:38px;color:var(--blue);
}
</style>
</head>
<body>
<main class="leaflet">
  <div class="stage-photo" role="img" aria-label="Faint stage photo of children dancing in costume"></div>

  <h1 class="headline">
    <span class="red">Award Wining</span><br>
    <span class="red">Classes in Drama</span><br>
    <span class="green">Singing &amp; Dance</span>
  </h1>

  <div class="brand">
    <span class="brand-dot"></span>
    <span class="brand-name">Bright Stage</span>
  </div>

  <div class="tags">
    <span class="tag blue">Award winning</span>
    <span class="tag yellow">accredited performing arts</span>
    <span class="tag red">provider KPM</span>
  </div>

  <p class="intro">are excited to bring you LIVE interactive drama, singing and dance parties taught by industry qualified performers that can be accessed from home</p>

  <svg class="swoosh" width="990" height="1403" viewBox="0 0 990 1403">
    <path d="M0,1403 L0,1358 C300,1335 380,1110 445,950 C525,730 660,640 990,650 L990,1403 Z" fill="#fff"/>
    <path d="M0,1358 C300,1335 380,1110 445,950 C525,730 660,640 990,650" fill="none" stroke="#ffc214" stroke-width="26"/>
  </svg>

  <div class="party-art" role="img" aria-label="Cartoon child dancing happily"></div>
  <div class="screen-art" role="img" aria-label="Computer screen showing a video call of children"></div>
  <div class="balloons" role="img" aria-label="Colourful party balloons and confetti"></div>

  <div class="price">
    <p class="lead">Packages<br>start from</p>
    <p class="amount">£65</p>
    <p class="vat">plus vat</p>
  </div>

  <ul class="features">
    <li class="feature" style="top:0">
      <svg width="62" height="50" viewBox="0 0 62 50"><circle cx="14" cy="34" r="10" fill="#fff"/><circle cx="34" cy="38" r="7" fill="#fff"/><circle cx="50" cy="18" r="10" fill="#ffc214"/></svg>
      <p>A chance for your child to hook<br>up with their classmates and<br>friends</p>
    </li>
    <li class="feature" style="top:105px">
      <svg width="62" height="62" viewBox="0 0 62 62"><rect x="4" y="4" width="54" height="20" rx="10" fill="none" stroke="#fff" stroke-width="3"/><rect x="4" y="32" width="54" height="26" rx="4" fill="#ffc214"/></svg>
      <p>An interactive hour of games,<br>dancing and singing amongst<br>friends as you talk, laugh and<br>play together on screen</p>
    </li>
    <li class="feature" style="top:238px">
      <svg width="62" height="56" viewBox="0 0 62 56"><path d="M20 4v20M40 4v20" stroke="#fff" stroke-width="3"/><rect x="8" y="30" width="46" height="22" fill="none" stroke="#ffc214" stroke-width="4"/></svg>
      <p>Tailor made themes, music<br>choices and routines</p>
    </li>
    <li class="feature" style="top:330px">
      <svg width="62" height="56" viewBox="0 0 62 56"><path d="M31 50 C10 36 4 26 4 17 C4 8 11 3 18 3 C24 3 29 7 31 12 C33 7 38 3 44 3 C51 3 58 8 58 17 C58 26 52 36 31 50 Z" fill="none" stroke="#ffc214" stroke-width="7"/></svg>
      <p>A chance to socialise in a<br>safe environment and<br>celebrate that special day</p>
    </li>
    <li class="feature" style="top:440px">
      <svg width="62" height="62" viewBox="0 0 62 62"><circle cx="31" cy="12" r="8" fill="none" stroke="#fff" stroke-width="3"/><rect x="6" y="28" width="50" height="30" rx="4" fill="none" stroke="#ffc214" stroke-width="4"/></svg>
      <p>All staff are qualified<br>DBS checked industry<br>professionals and<br>teachers</p>
    </li>
    <li class="feature" style="top:565px">
      <svg width="62" height="56" viewBox="0 0 62 56"><path d="M6 8h18l5 6h27v38H6Z" fill="none" stroke="#ffc214" stroke-width="4"/><path d="M31 44V24M22 32l9-9 9 9" fill="none" stroke="#fff" stroke-width="4"/></svg>
      <p>Flexible times<br>to suit</p>
    </li>
  </ul>

  <span class="book-pill">to book</span>
  <div class="visit-bar">
    <svg width="32" height="32" viewBox="0 0 34 34" fill="none" stroke="#fff" stroke-width="2.5"><circle cx="17" cy="17" r="14"/><ellipse cx="17" cy="17" rx="6" ry="14"/><path d="M3 17h28M6 9h22M6 25h22"/></svg>
    <span>Visit www.brightstagehub.co.uk</span>
  </div>
  <p class="sessions">Check out our online performing arts<br>classes and interactive sessions</p>
</main>
</body>
</html>
```